Business card design for international hub site

I need a business card design with the logo attached. Although the site is for the teenage audience (it is about the high school graduation ball, the Prom), the business card is for professional use to be given to professional contacts (B2B), such as suppliers and partners, so it needs to look professional (but also girly, glamours and clean).

Target Market(s)

B2B

Industry/Entity Type

Media

Colors
eea4c8
f9d9e8
e667a6
9d9d9d
1b1b1b

Requirements
Must have
• Space for Name, Tile, Address, Phone, email and website.
Should not have
• Photo

```html
<!DOCTYPE html>
<html lang="en">
<head>
<meta charset="utf-8">
<title>Belle Night — Business Card</title>
<link rel="stylesheet" href="https://fonts.googleapis.com/css2?family=EB+Garamond:wght@400;500&family=Pinyon+Script&display=swap">
<style>
  :root {
    --pink-deep: #e63c7c;
    --pink-accent: #f0649f;
    --pink-soft: #f9d9e8;
    --ink: #1b1b1b;
    --band-dark: #2b2b2b;
    --paper: #ffffff;
    --stage: #ececec;
    --muted: #9d9d9d;
    --serif: "EB Garamond", Georgia, serif;
    --script: "Pinyon Script", cursive;
  }
  * { box-sizing: border-box; margin: 0; padding: 0; }
  html, body { width: 1200px; height: 586px; overflow: hidden; }
  body {
    background: var(--stage);
    font-family: var(--serif);
    position: relative;
  }
  .card {
    position: absolute;
    top: 128px;
    width: 501px;
    height: 294px;
    overflow: hidden;
  }
  .card--front { left: 65px; background: var(--pink-deep); }
  .card--back { left: 608px; background: var(--paper); }

  .band {
    position: absolute;
    left: 0; right: 0;
    top: 208px;
    height: 59px;
  }
  .card--front .band { background: var(--paper); }
  .card--back .band { background: var(--band-dark); }

  .ornament {
    position: absolute;
    top: 120px;
    width: 280px;
    height: 160px;
  }
  .card--front .ornament {
    left: 225px;
    background: radial-gradient(ellipse 50% 50% at 55% 45%,
      rgba(255, 255, 255, 0.30) 0%,
      rgba(255, 255, 255, 0.14) 45%,
      rgba(255, 255, 255, 0) 100%);
  }
  .card--back .ornament {
    left: 0;
    background: radial-gradient(ellipse 50% 50% at 50% 45%,
      rgba(27, 27, 27, 0.16) 0%,
      rgba(27, 27, 27, 0.07) 45%,
      rgba(27, 27, 27, 0) 100%);
  }

  .brand-name {
    position: absolute;
    left: 64px; top: 40px;
    color: var(--paper);
    font-family: var(--serif);
    font-weight: 400;
    font-size: 44px;
    line-height: 0.92;
    letter-spacing: 0.5px;
  }
  .brand-name span { display: block; }
  .brand-name span + span { padding-left: 34px; }

  .person-name {
    position: absolute;
    left: 30px; top: 30px;
    font-family: var(--script);
    font-size: 30px;
    color: var(--pink-accent);
    font-weight: 400;
    white-space: nowrap;
  }

  .contact-list {
    position: absolute;
    right: 38px; top: 74px;
    list-style: none;
    text-align: right;
  }
  .contact-list li {
    display: flex;
    justify-content: flex-end;
    align-items: center;
    gap: 10px;
    font-size: 11.5px;
    color: var(--ink);
    height: 24.5px;
    white-space: nowrap;
  }
  .contact-list svg { width: 13px; height: 12px; fill: var(--pink-accent); }

  .address {
    position: absolute;
    right: 40px; top: 150px;
    text-align: right;
    font-style: normal;
    font-size: 12px;
    line-height: 18px;
    color: var(--pink-accent);
    white-space: nowrap;
  }
  .website {
    position: absolute;
    right: 40px; top: 229px;
    font-size: 12.5px;
    letter-spacing: 2.4px;
    color: var(--pink-accent);
    white-space: nowrap;
  }
</style>
</head>
<body>

  <section class="card card--front" aria-label="Card front">
    <div class="band"></div>
    <div class="ornament" role="img" aria-label="White flourish ornament of curling swirls and leaves"></div>
    <h1 class="brand-name"><span>belle</span><span>night</span></h1>
  </section>

  <section class="card card--back" aria-label="Card back">
    <div class="band"></div>
    <div class="ornament" role="img" aria-label="Dark flourish ornament of curling swirls and leaves"></div>
    <h2 class="person-name">Maren Holloway</h2>

    <ul class="contact-list">
      <li>+44 (0)1632 960417
        <svg viewBox="0 0 13 12" aria-label="Phone"><path d="M1 4.5C1 2.5 3.5 1 6.5 1S12 2.5 12 4.5v1H9.5V4H3.5v1.5H1z"/><path d="M3 6.5h7l1.5 4.5h-10z"/></svg>
      </li>
      <li>(555) 014-2297
        <svg viewBox="0 0 13 12" aria-label="Fax"><rect x="3.5" y="0.5" width="6" height="3"/><rect x="0.5" y="4" width="12" height="5" rx="1"/><rect x="3.5" y="8" width="6" height="3.5"/></svg>
      </li>
      <li>hello@bellenight.com
        <svg viewBox="0 0 13 12" aria-label="Email"><path d="M0.5 2h12v8h-12z"/><path d="M0.5 2l6 4.5 6-4.5" fill="none" stroke="#fff" stroke-width="1"/></svg>
      </li>
    </ul>

    <address class="address">Linden Court, Ashby<br>Marlow, ZZ1 4QT</address>
    <p class="website">www.bellenight.com</p>
  </section>

</body>
</html>
```